Business card for event manager / organizer "waiter service"

Draft of a new valuable business card for my company.
Events, personnel service providers, festivals

```html
<!DOCTYPE html>
<html lang="de">
<head>
<meta charset="utf-8">
<title>Brenner Servicecrew – Visitenkarte</title>
<link href="https://fonts.googleapis.com/css2?family=Montserrat:wght@400;500;700;800&display=swap" rel="stylesheet">
<style>
  :root {
    --backdrop: #d9d9d9;
    --card-dark-top: #221f1f;
    --card-dark-bottom: #131111;
    --gold: #c9a45f;
    --gold-soft: #b8955a;
    --white: #ffffff;
    --ink: #151515;
    --accent: #e8731e;
    --muted: #6b6b6b;
    --photo-low: #3b3f4a;
  }
  * { box-sizing: border-box; margin: 0; padding: 0; }
  html, body {
    width: 1200px; height: 1200px; overflow: hidden;
    background: var(--backdrop);
    font-family: "Montserrat", sans-serif;
  }
  .canvas {
    width: 1200px; height: 1200px;
    display: flex; flex-direction: column; align-items: center; justify-content: center;
    gap: 60px;
  }
  .card {
    position: relative;
    width: 860px; height: 491px;
    overflow: hidden;
    box-shadow: 0 10px 30px rgba(0,0,0,.18);
  }
  /* Front */
  .card-front {
    background: linear-gradient(180deg, var(--card-dark-top), var(--card-dark-bottom));
  }
  .gold-band {
    position: absolute; left: 200px; top: 20px;
    width: 220px; height: 180px;
    background: var(--gold);
  }
  .portrait {
    position: absolute; left: 200px; top: 20px;
    width: 220px; height: 270px;
    border-radius: 0 0 110px 110px;
    background: linear-gradient(180deg, var(--gold) 0%, var(--gold-soft) 35%, var(--photo-low) 100%);
  }
  .identity {
    position: absolute; left: 500px; top: 160px; width: 320px;
    color: var(--gold);
  }
  .identity-name { font-size: 32px; font-weight: 700; line-height: 1.1; }
  .identity-role { font-size: 19px; font-weight: 400; margin-top: 4px; }
  .identity-rule { height: 3px; background: var(--gold); width: 280px; margin-top: 10px; }
  .contact-list {
    position: absolute; left: 480px; top: 296px;
    list-style: none; color: var(--gold);
    font-size: 18px; font-weight: 500; line-height: 1.5;
  }
  .contact-item { display: flex; align-items: center; gap: 10px; white-space: nowrap; }
  .contact-icon { width: 17px; height: 17px; flex: none; fill: var(--gold); }
  /* Back */
  .card-back {
    background: var(--white);
    display: flex; flex-direction: column; align-items: center; justify-content: center;
  }
  .brand { display: flex; align-items: center; gap: 20px; }
  .brand-square { width: 64px; height: 64px; background: var(--accent); flex: none; }
  .brand-name {
    font-size: 42px; font-weight: 800; color: var(--ink);
    text-transform: uppercase; letter-spacing: 1px; line-height: 1; white-space: nowrap;
  }
  .brand-tagline {
    margin-top: 18px; padding-left: 84px;
    font-size: 19px; font-weight: 400; color: var(--muted); white-space: nowrap;
  }
</style>
</head>
<body>
<main class="canvas">
  <section class="card card-front">
    <div class="gold-band"></div>
    <div class="portrait" role="img" aria-label="Porträtfoto des Inhabers in Hemd und Weste"></div>
    <div class="identity">
      <h1 class="identity-name">Jonas Brenner</h1>
      <p class="identity-role">Inhaber</p>
      <div class="identity-rule"></div>
    </div>
    <ul class="contact-list">
      <li class="contact-item">
        <svg class="contact-icon" viewBox="0 0 24 24"><path d="M6.6 10.8a15 15 0 0 0 6.6 6.6l2.2-2.2a1 1 0 0 1 1-.25 11.4 11.4 0 0 0 3.6.57 1 1 0 0 1 1 1V20a1 1 0 0 1-1 1A17 17 0 0 1 3 4a1 1 0 0 1 1-1h3.5a1 1 0 0 1 1 1c0 1.25.2 2.45.57 3.6a1 1 0 0 1-.25 1z"/></svg>
        02361 555 01 23
      </li>
      <li class="contact-item">
        <svg class="contact-icon" viewBox="0 0 24 24"><path d="M6.6 10.8a15 15 0 0 0 6.6 6.6l2.2-2.2a1 1 0 0 1 1-.25 11.4 11.4 0 0 0 3.6.57 1 1 0 0 1 1 1V20a1 1 0 0 1-1 1A17 17 0 0 1 3 4a1 1 0 0 1 1-1h3.5a1 1 0 0 1 1 1c0 1.25.2 2.45.57 3.6a1 1 0 0 1-.25 1z"/></svg>
        0170 555 48 26
      </li>
      <li class="contact-item">
        <svg class="contact-icon" viewBox="0 0 24 24"><path d="M2 5h20v14H2z"/><path d="M3 6l9 7 9-7" fill="none" stroke="#131111" stroke-width="1.6"/></svg>
        info@brenner-servicecrew.de
      </li>
      <li class="contact-item">
        <svg class="contact-icon" viewBox="0 0 24 24"><circle cx="12" cy="12" r="10" fill="none" style="stroke:var(--gold)" stroke-width="2"/><path d="M2 12h20M12 2c3 3 3 17 0 20M12 2c-3 3-3 17 0 20" fill="none" style="stroke:var(--gold)" stroke-width="1.6"/></svg>
        www.brenner-servicecrew.de
      </li>
      <li class="contact-item">
        <svg class="contact-icon" viewBox="0 0 24 24"><path d="M12 2a7 7 0 0 0-7 7c0 5 7 13 7 13s7-8 7-13a7 7 0 0 0-7-7zm0 9.5a2.5 2.5 0 1 1 0-5 2.5 2.5 0 0 1 0 5z"/></svg>
        Lindenweg 12, 45700 Musterstadt
      </li>
      <li class="contact-item">
        <svg class="contact-icon" viewBox="0 0 24 24"><circle cx="12" cy="12" r="9"/></svg>
        brennerservicecrew
      </li>
    </ul>
  </section>

  <section class="card card-back">
    <div class="brand">
      <div class="brand-square"></div>
      <h2 class="brand-name">Brenner Servicecrew</h2>
    </div>
    <p class="brand-tagline">…weil jedes Fest guten Service verdient!</p>
  </section>
</main>
</body>
</html>
```